Business Card Design for Training Business

Clear Path Coaching is a new business that delivers training and other services with a focus on topics related to mental health and wellbeing, for example, Wellmind Response Course, Resilience etc. We have a strong focus on evidence-based psychology and neuroscience. I have a logo which I will upload with the brief, so please consider colours that work well with the logo.
Target Market(s)
Adults, workplaces (particularly government and not-for-profits)
Industry/Entity Type
Business
Contact Information for Business Card
Head Strong TrainingSamantha SellwoodDirector0438 770 850sam@headstrongtraining.com.auwww.headstrongtraining.com.au

```html
<!DOCTYPE html>
<html lang="en">
<head>
<meta charset="utf-8">
<title>Clear Path Coaching – Business Card</title>
<link rel="stylesheet" href="https://fonts.googleapis.com/css2?family=Open+Sans:wght@300;400;600&display=swap">
<style>
  :root {
    --backdrop: #e9e6e1;
    --card: #ffffff;
    --teal: #5bc5cb;
    --ink: #1a1a1a;
    --muted: #8a8a8a;
  }
  * { margin: 0; padding: 0; box-sizing: border-box; }
  html, body {
    width: 1200px; height: 858px; overflow: hidden;
    background: var(--backdrop);
    font-family: "Open Sans", Arial, sans-serif;
  }
  .card {
    position: absolute; left: 250px; top: 215px;
    width: 700px; height: 428px;
    background: var(--card);
    box-shadow: 0 10px 30px rgba(0,0,0,.18);
    overflow: hidden;
  }
  .corner-bands { position: absolute; inset: 0; }
  .brand {
    position: absolute; left: 190px; top: 88px;
    display: flex; align-items: center; gap: 22px;
  }
  .brand-mark {
    width: 100px; height: 100px; border-radius: 50%;
    border: 2px solid var(--teal);
  }
  .brand-name {
    font-weight: 300; color: var(--muted);
    font-size: 34px; letter-spacing: 4px; text-transform: uppercase; line-height: 1.1;
  }
  .details {
    position: absolute; left: 0; right: 0; top: 248px;
    display: flex; align-items: stretch;
  }
  .person {
    width: 318px; text-align: right; padding-right: 18px; padding-top: 14px;
  }
  .person-name { font-weight: 600; font-size: 24px; color: var(--ink); }
  .person-role { font-weight: 600; font-size: 18px; color: var(--ink); margin-top: 2px; }
  .divider { width: 2px; background: var(--teal); }
  .contacts { list-style: none; padding-left: 16px; padding-top: 4px; }
  .contacts li {
    display: flex; align-items: center; gap: 8px;
    font-size: 17px; color: var(--ink); line-height: 30px;
  }
  .contact-icon {
    width: 16px; height: 16px; background: var(--ink); border-radius: 2px;
    display: inline-flex; align-items: center; justify-content: center;
  }
</style>
</head>
<body>
  <section class="card">
    <svg class="corner-bands" width="700" height="428" viewBox="0 0 700 428" aria-hidden="true">
      <polygon points="530,0 620,0 700,125 700,250" fill="var(--teal)"/>
      <polygon points="620,0 700,0 700,125" fill="var(--ink)"/>
      <polygon points="0,178 0,303 80,428 170,428" fill="var(--teal)"/>
      <polygon points="0,303 0,428 80,428" fill="var(--ink)"/>
    </svg>

    <div class="brand">
      <span class="brand-mark"></span>
      <span class="brand-name">Clear Path<br>Coaching</span>
    </div>

    <div class="details">
      <div class="person">
        <p class="person-name">Rebecca Tanfield</p>
        <p class="person-role">Director</p>
      </div>
      <span class="divider"></span>
      <ul class="contacts">
        <li>
          <span class="contact-icon">
            <svg width="10" height="10" viewBox="0 0 10 10"><path d="M2 1 L4 1 L4.5 3 L3.5 4 Q4.5 6 6 6.5 L7 5.5 L9 6 L9 8 Q5 9 2 5 Q1 3 2 1Z" fill="#fff"/></svg>
          </span>0491 362 517
        </li>
        <li>
          <span class="contact-icon">
            <svg width="10" height="10" viewBox="0 0 10 10"><rect x="1" y="2.5" width="8" height="5" fill="none" stroke="#fff"/><path d="M1 2.5 L5 5.5 L9 2.5" fill="none" stroke="#fff"/></svg>
          </span>bec@clearpathcoaching.example.au
        </li>
        <li>
          <span class="contact-icon">
            <svg width="10" height="10" viewBox="0 0 10 10"><circle cx="5" cy="5" r="3.8" fill="none" stroke="#fff"/><ellipse cx="5" cy="5" rx="1.6" ry="3.8" fill="none" stroke="#fff"/><line x1="1.2" y1="5" x2="8.8" y2="5" stroke="#fff"/></svg>
          </span>www.clearpathcoaching.example.au
        </li>
      </ul>
    </div>
  </section>
</body>
</html>
```